Redesign of business card for Cedar Ridge Mechanical

We are looking for a new design for our business cards for Cedar Ridge Mechanical. We are a plumbing & HVAC construction company, operating on the West Coast of Canada and USA. Logo attached.
Industry/Entity Type
Construction - Plumbing & HVAC
Contact Information for Business Card
Name, address, phone numbers, email, website address
Look and feel
Each slider illustrates characteristics of the customer's brand and the style your logo design should communicate.

```html
<!DOCTYPE html>
<html lang="en">
<head>
<meta charset="utf-8">
<title>Cedar Ridge Mechanical – Business Card</title>
<link href="https://fonts.googleapis.com/css2?family=Montserrat:wght@400;700&family=Oswald:wght@600&display=swap" rel="stylesheet">
<style>
  :root {
    --stage: #1b1b1b;
    --card: #121212;
    --card-edge: #2a2a2a;
    --ink: #ffffff;
    --ink-dark: #3a3a3a;
    --band: #f4f4f4;
    --band-shade: #8a8a8a;
    --pattern-a: #1a1a1a;
    --pattern-b: #262626;
  }
  * { box-sizing: border-box; margin: 0; padding: 0; }
  html, body { width: 1200px; height: 963px; overflow: hidden; background: var(--stage); }
  .stage {
    width: 1200px; height: 963px;
    display: flex; flex-direction: column; align-items: center; justify-content: center; gap: 34px;
  }
  .card {
    position: relative; width: 760px; height: 434px;
    background: var(--card); border-radius: 26px; overflow: hidden;
    box-shadow: 0 0 0 1px var(--card-edge);
    font-family: "Montserrat", sans-serif; color: var(--ink);
  }

  /* Front */
  .brand {
    position: absolute; left: 60px; top: 58px;
    display: flex; align-items: center; gap: 16px;
  }
  .brand-square { width: 46px; height: 46px; border: 0; background: var(--ink); }
  .brand-name {
    font-family: "Oswald", sans-serif; font-weight: 600; font-size: 30px;
    letter-spacing: 1px; text-transform: uppercase; line-height: 1.1;
  }
  .divider {
    position: absolute; left: 60px; right: 60px; top: 240px;
    height: 2px; background: var(--ink);
  }
  .person {
    position: absolute; right: 60px; top: 170px; text-align: right;
  }
  .person-name { font-weight: 700; font-size: 27px; letter-spacing: 1px; text-transform: uppercase; }
  .person-role { font-size: 17px; margin-top: 2px; }
  .contact {
    position: absolute; left: 60px; top: 262px; list-style: none;
    font-size: 18px; line-height: 30px;
  }
  .contact li { display: flex; align-items: center; gap: 10px; }
  .contact svg { width: 16px; height: 16px; fill: var(--ink); }
  .address {
    position: absolute; right: 60px; top: 262px; text-align: right;
    font-size: 18px; line-height: 26px;
  }
  .band { position: absolute; left: 0; bottom: 0; width: 760px; height: 70px; }
  .website {
    position: absolute; right: 60px; bottom: 14px;
    font-size: 19px; color: var(--ink-dark);
  }

  /* Back */
  .pattern-field {
    position: absolute; inset: 0;
    background: linear-gradient(135deg, var(--pattern-b), var(--pattern-a) 60%, var(--pattern-b));
  }
  .back-title {
    position: absolute; left: 60px; top: 42px;
    font-family: "Oswald", sans-serif; font-weight: 600; font-size: 54px;
    letter-spacing: 3px; text-transform: uppercase;
  }
</style>
</head>
<body>
<main class="stage">
  <section class="card card-front">
    <div class="brand">
      <span class="brand-square"></span>
      <span class="brand-name">Cedar Ridge Mechanical</span>
    </div>

    <div class="person">
      <p class="person-name">Daniel Harper</p>
      <p class="person-role">Manager</p>
    </div>

    <div class="divider"></div>

    <ul class="contact">
      <li>
        <svg viewBox="0 0 24 24" aria-hidden="true"><path d="M6.6 10.8a15.1 15.1 0 0 0 6.6 6.6l2.2-2.2a1 1 0 0 1 1-.25 11.4 11.4 0 0 0 3.6.57 1 1 0 0 1 1 1V20a1 1 0 0 1-1 1A17 17 0 0 1 3 4a1 1 0 0 1 1-1h3.5a1 1 0 0 1 1 1c0 1.25.2 2.45.57 3.57a1 1 0 0 1-.25 1z"/></svg>
        123-456-2100
      </li>
      <li>
        <svg viewBox="0 0 24 24" aria-hidden="true"><path d="M2 5h20v14H2zm2 2v.5l8 5 8-5V7zm0 2.8V17h16V9.8l-8 5z"/></svg>
        youremail@cedarridgemech.com
      </li>
    </ul>

    <p class="address">Your address, city<br>state, ZIP 0000</p>

    <svg class="band" viewBox="0 0 760 70" aria-hidden="true">
      <path d="M0 56 H400 C420 56 425 38 450 38 H760 V70 H0 Z" fill="var(--band)"/>
      <path d="M0 50 H395 L402 56 H0 Z" fill="var(--band-shade)"/>
    </svg>
    <p class="website">www.yourwebsite.com</p>
  </section>

  <section class="card card-back">
    <div class="pattern-field" role="img" aria-label="Tonal repeating brand pattern across the card back"></div>
    <p class="back-title">Cedar Ridge Mechanical</p>
  </section>
</main>
</body>
</html>
```